Design a Travel and Tourism website

We would like a freelancer to design a website that is essentially easy to use and navigate database providing local information for Travelers about destination countries.

We proposed website would discuss different rates, fees, visa requirement, resort locations, cheap flights, etc. This website should be elegant and modern. Our business name is rovanix.
Some reference websites are zemplorift.ca, brindlefoxhaven.com,
There should be a forum in the website where travell\ers discuss about their first hand tranvel experience to such destinations.

Tourism

```html
<!DOCTYPE html>
<html lang="en">
<head>
<meta charset="utf-8">
<title>Rovanix — Travel &amp; Tourism</title>
<link href="https://fonts.googleapis.com/css2?family=Roboto:wght@300;400;500;700&display=swap" rel="stylesheet">
<style>
:root{
  --orange:#ef6a2c;
  --orange-dark:#e1561a;
  --ink:#222;
  --text:#555;
  --muted:#777;
  --line:#e3e3e3;
  --soft:#f4f4f4;
  --white:#fff;
}
*{box-sizing:border-box;margin:0;padding:0}
html,body{width:1200px;height:2632px;overflow:hidden}
body{position:relative;background:var(--white);font-family:"Roboto",sans-serif;color:var(--text)}
.abs{position:absolute}

/* header */
.site-header{position:absolute;left:0;top:0;width:1200px;height:67px;background:var(--white);border-bottom:1px solid #ddd}
.brand{position:absolute;left:53px;top:14px;font-size:34px;font-weight:700;color:var(--orange);letter-spacing:-0.5px}
.main-nav{position:absolute;top:27px;left:0;width:1200px;font-size:13px;color:#555}
.main-nav span{position:absolute}
.header-icon{position:absolute;top:26px}

/* hero */
.hero{position:absolute;left:0;top:67px;width:1200px;height:684px;
  background:linear-gradient(180deg,#3c5a9a 0%,#5570a8 30%,#7a84a6 52%,#b98e62 68%,#6c5546 82%,#3a3340 100%)}
.hero-dots{position:absolute;left:1158px;top:355px}
.hero-dots i{display:block;width:7px;height:7px;border-radius:50%;background:rgba(255,255,255,.55);margin-bottom:20px}

.search-tabs{position:absolute;left:100px;top:424px;height:39px;display:flex}
.search-tab{height:39px;background:var(--orange);color:#fff;font-size:13px;display:flex;align-items:center;justify-content:center;gap:8px;border-right:1px solid rgba(255,255,255,.35)}
.search-tab svg{width:18px;height:18px}
.search-panel{position:absolute;left:100px;top:463px;width:1000px;height:268px;background:rgba(255,255,255,.93)}
.field-label{position:absolute;font-size:13px;color:#333}
.field{position:absolute;height:38px;background:#fff;border:1px solid #d6d6d6;font-size:12px;color:#999;display:flex;align-items:center;padding-left:14px;gap:7px}
.field .caret{position:absolute;right:12px;top:14px}
.check{position:absolute;left:124px;top:668px;width:18px;height:18px;border:1px solid #bbb;background:#fff}
.btn{position:absolute;background:var(--orange);color:#fff;font-weight:500;display:flex;align-items:center;justify-content:center;text-transform:uppercase}

/* features */
.feature{position:absolute;width:320px;text-align:center}
.feature-icon{width:68px;height:68px;border-radius:50%;background:var(--orange);margin:0 auto;display:flex;align-items:center;justify-content:center}
.feature h3{font-size:17px;font-weight:500;color:var(--ink);margin-top:26px}
.feature p{font-size:11.5px;line-height:21px;color:#666;margin-top:12px}

.section-title{position:absolute;left:100px;font-size:25px;font-weight:500;color:var(--ink)}
.section-lede{position:absolute;left:100px;font-size:11.5px;color:#555}

.deal-card{position:absolute;top:1175px;width:314px;height:316px}
.deal-card span{position:absolute;left:18px;bottom:20px;color:#fff;font-size:17px;font-weight:300;border-left:4px solid var(--orange);padding-left:8px;line-height:18px}
.pager{position:absolute;left:578px;top:1526px;display:flex;gap:5px}
.pager i{width:6px;height:6px;border-radius:50%;background:#ccc}
.pager i.on{background:var(--orange)}

.activities{position:absolute;left:0;top:1587px;width:1200px;height:500px;background:var(--soft)}
.activity{position:absolute;top:1740px;width:236px}
.activity .photo{height:210px}
.activity h4{margin-top:20px;font-size:13px;font-weight:700;color:var(--ink);border-left:4px solid var(--orange);padding-left:12px;line-height:16px}
.activity .loc{font-size:10.5px;color:#666;margin:7px 0 0 14px}
.activity .price{display:flex;justify-content:space-between;margin-top:10px;padding-left:14px;font-size:13px;color:#555}
.activity .price b{color:var(--orange);font-size:16px;font-weight:500}
.stars{color:var(--orange);font-size:10px;letter-spacing:1px;margin-top:4px}

.favorites{position:absolute;top:2220px;font-size:12px;color:#555;line-height:30px;list-style:none}

.footer-rule{position:absolute;left:0;top:2438px;width:1200px;height:1px;background:var(--line)}
.copyright{position:absolute;left:100px;top:2474px;font-size:12px;color:#444}
.social-label{position:absolute;left:708px;top:2474px;font-size:12px;color:#444}
.social{position:absolute;top:2462px;width:36px;height:36px;border-radius:50%}
.footer-note{position:absolute;left:100px;top:2524px;width:1000px;font-size:11.5px;line-height:21px;color:#555}
</style>
</head>
<body>

<header class="site-header">
  <div class="brand">Rovanix</div>
  <nav class="main-nav">
    <span style="left:253px">Flight + Hotel</span>
    <span style="left:375px">Vacations</span>
    <span style="left:480px">Hotels</span>
    <span style="left:565px">Cars</span>
    <span style="left:640px">Flights</span>
    <span style="left:726px">Things to Do</span>
    <span style="left:846px">Deals</span>
    <span style="left:914px">My Account</span>
    <span style="left:1023px">sign in</span>
  </nav>
  <svg class="header-icon" style="left:1084px" width="16" height="16" viewBox="0 0 16 16"><circle cx="6.5" cy="6.5" r="5" fill="none" stroke="#666" stroke-width="1.6"/><line x1="10" y1="10" x2="15" y2="15" stroke="#666" stroke-width="1.6"/></svg>
  <svg class="header-icon" style="left:1127px" width="18" height="16" viewBox="0 0 18 16"><path d="M1 5h16l-2 10H3z" fill="none" stroke="#666" stroke-width="1.5"/><path d="M5 5l4-4 4 4" fill="none" stroke="#666" stroke-width="1.5"/></svg>
</header>

<div class="hero" role="img" aria-label="Evening photo of a historic twin-towered bascule bridge over a river under a blue sky"></div>
<div class="hero-dots"><i></i><i></i><i></i><i></i></div>

<div class="search-tabs">
  <div class="search-tab" style="width:93px"><svg viewBox="0 0 20 20"><path d="M2 11l16-7-3 6 3 4-5-1-5 4 1-5z" fill="#fff"/></svg>Fights</div>
  <div class="search-tab" style="width:98px"><svg viewBox="0 0 20 20"><rect x="4" y="2" width="12" height="16" fill="none" stroke="#fff" stroke-width="1.6"/><path d="M7 6h2M11 6h2M7 10h2M11 10h2" stroke="#fff" stroke-width="1.6"/></svg>Hotels</div>
  <div class="search-tab" style="width:151px"><svg viewBox="0 0 20 20"><path d="M10 2l7 4v8l-7 4-7-4V6z M3 6l7 4 7-4 M10 10v8" fill="none" stroke="#fff" stroke-width="1.5"/></svg>Bundle Deals</div>
  <div class="search-tab" style="width:93px"><svg viewBox="0 0 20 20"><path d="M3 12l2-5h10l2 5v4H3z" fill="none" stroke="#fff" stroke-width="1.6"/><circle cx="6.5" cy="14" r="1.3" fill="#fff"/><circle cx="13.5" cy="14" r="1.3" fill="#fff"/></svg>Cars</div>
  <div class="search-tab" style="width:110px;border-right:0"><svg viewBox="0 0 20 20"><circle cx="12" cy="3" r="2" fill="#fff"/><path d="M5 8l5-2 3 3-2 4 3 5M10 6l-2 6-5 5M13 9l4 1" fill="none" stroke="#fff" stroke-width="1.8"/></svg>Activities</div>
</div>

<section class="search-panel" aria-label="Search"></section>
<div class="field-label" style="left:124px;top:486px">Flying From</div>
<div class="field" style="left:122px;top:516px;width:472px"><svg width="9" height="12" viewBox="0 0 9 12"><path d="M4.5 0a4.5 4.5 0 0 1 4.5 4.5C9 8 4.5 12 4.5 12S0 8 0 4.5A4.5 4.5 0 0 1 4.5 0z" fill="#aaa"/><circle cx="4.5" cy="4.5" r="1.6" fill="#fff"/></svg>City or airport</div>
<div class="field-label" style="left:608px;top:486px">Flying to</div>
<div class="field" style="left:606px;top:516px;width:472px"><svg width="9" height="12" viewBox="0 0 9 12"><path d="M4.5 0a4.5 4.5 0 0 1 4.5 4.5C9 8 4.5 12 4.5 12S0 8 0 4.5A4.5 4.5 0 0 1 4.5 0z" fill="#aaa"/><circle cx="4.5" cy="4.5" r="1.6" fill="#fff"/></svg>City or airport</div>

<div class="field-label" style="left:124px;top:572px">Departing</div>
<div class="field" style="left:122px;top:602px;width:232px"><svg width="12" height="12" viewBox="0 0 12 12"><rect x="1" y="2" width="10" height="9" fill="none" stroke="#aaa"/><line x1="1" y1="5" x2="11" y2="5" stroke="#aaa"/></svg>mm/dd/yyyy</div>
<div class="field-label" style="left:364px;top:572px">Returning</div>
<div class="field" style="left:362px;top:602px;width:232px"><svg width="12" height="12" viewBox="0 0 12 12"><rect x="1" y="2" width="10" height="9" fill="none" stroke="#aaa"/><line x1="1" y1="5" x2="11" y2="5" stroke="#aaa"/></svg>mm/dd/yyyy</div>
<div class="field-label" style="left:608px;top:572px">Rooms</div>
<div class="field" style="left:606px;top:602px;width:150px">1<svg class="caret" width="9" height="6" viewBox="0 0 9 6"><path d="M1 1l3.5 3.5L8 1" fill="none" stroke="#666" stroke-width="1.3"/></svg></div>
<div class="field-label" style="left:768px;top:572px">Adults (18+)</div>
<div class="field" style="left:766px;top:602px;width:150px">2<svg class="caret" width="9" height="6" viewBox="0 0 9 6"><path d="M1 1l3.5 3.5L8 1" fill="none" stroke="#666" stroke-width="1.3"/></svg></div>
<div class="field-label" style="left:928px;top:572px">Children (0-17)</div>
<div class="field" style="left:926px;top:602px;width:152px">0<svg class="caret" width="9" height="6" viewBox="0 0 9 6"><path d="M1 1l3.5 3.5L8 1" fill="none" stroke="#666" stroke-width="1.3"/></svg></div>

<div class="check"></div>
<div class="abs" style="left:154px;top:669px;font-size:13px;color:#333">I only need a hotel for part of my stay</div>
<div class="abs" style="left:411px;top:673px;font-size:12px;color:var(--orange)">Advanced options</div>
<div class="field" style="left:538px;top:662px;width:228px;color:#777">Economy / Coach<svg class="caret" width="9" height="6" viewBox="0 0 9 6"><path d="M1 1l3.5 3.5L8 1" fill="none" stroke="#666" stroke-width="1.3"/></svg></div>
<div class="btn" style="left:779px;top:664px;width:132px;height:38px;font-size:14px;gap:8px"><svg width="15" height="15" viewBox="0 0 16 16"><circle cx="6.5" cy="6.5" r="5" fill="none" stroke="#fff" stroke-width="2"/><line x1="10" y1="10" x2="15" y2="15" stroke="#fff" stroke-width="2"/></svg>Search</div>
<div class="abs" style="left:928px;top:674px;width:13px;height:13px;background:var(--orange)"><svg width="13" height="13" viewBox="0 0 13 13"><path d="M6.5 3v7M3 6.5h7" stroke="#fff" stroke-width="1.6"/></svg></div>
<div class="abs" style="left:950px;top:673px;font-size:12px;color:var(--orange)">More Search Options</div>

<div class="feature" style="left:98px;top:811px">
  <div class="feature-icon"><svg width="34" height="34" viewBox="0 0 34 34"><path d="M17 14c-4-6-10-5-12-2 4-1 7 0 9 2-4 0-8 3-8 7 3-3 6-4 9-4l1 12h3l-1-12c3 0 6 1 9 4 0-4-4-7-8-7 2-2 5-3 9-2-2-3-8-4-12 2z" fill="#fff"/><path d="M5 29h24" stroke="#fff" stroke-width="2"/></svg></div>
  <h3>Summer deals</h3>
  <p>Lorem Ipsum is simply dummy text of the printing and typesetting industry. Lorem Ipsum has been the industry's standard dummy text ever since the 1500s</p>
</div>
<div class="feature" style="left:440px;top:811px">
  <div class="feature-icon"><svg width="34" height="34" viewBox="0 0 34 34"><path d="M28 6c-2-2-5 0-7 2l-4 4-11-3-2 2 9 5-4 5-4-1-1 1 4 3 3 4 1-1-1-4 5-4 5 9 2-2-3-11 4-4c2-2 4-5 2-7z" fill="#fff"/></svg></div>
  <h3>City breaks</h3>
  <p>Lorem Ipsum is simply dummy text of the printing and typesetting industry. Lorem Ipsum has been the industry's standard dummy text ever since the 1500s</p>
</div>
<div class="feature" style="left:800px;top:811px">
  <div class="feature-icon"><svg width="34" height="34" viewBox="0 0 34 34"><path d="M17 4l12 6v14l-12 6-12-6V10z M5 10l12 6 12-6 M17 16v14 M11 7l12 6" fill="none" stroke="#fff" stroke-width="2"/></svg></div>
  <h3>All inclusive</h3>
  <p>Lorem Ipsum is simply dummy text of the printing and typesetting industry. Lorem Ipsum has been the indus-try's standard dummy text ever since the 1500s</p>
</div>

<h2 class="section-title" style="top:1084px">TODAY'S TOP DEALS</h2>
<p class="section-lede" style="top:1129px">Lorem Ipsum is simply dummy text of the printing and typesetting industry. Lorem Ipsum has been the industry's standard dummy text ever since the 1500s</p>
<div class="btn" style="left:945px;top:1110px;width:156px;height:37px;font-size:11px">View more deals</div>

<div class="deal-card" style="left:100px;background:linear-gradient(180deg,#caa070 0%,#e0a24e 35%,#6b5a4e 65%,#2d2a2e 100%)" role="img" aria-label="City skyline and bridge at sunset"><span>Extra Savings on Your Escape</span></div>
<div class="deal-card" style="left:444px;background:linear-gradient(180deg,#3d8fd8 0%,#6cb2e6 40%,#8a7258 58%,#1ea6c9 75%,#0b6f92 100%)" role="img" aria-label="Overwater bungalows with a turquoise pool and palm tree"><span>Today's 24 Hour Sale</span></div>
<div class="deal-card" style="left:788px;background:linear-gradient(180deg,#f2a23a 0%,#e57e27 40%,#b35e2a 65%,#5a4a44 100%)" role="img" aria-label="Couple in a convertible on a sunset road"><span>Winter Escapes</span></div>
<div class="pager"><i class="on"></i><i></i><i></i><i></i></div>

<section class="activities"></section>
<h2 class="section-title" style="top:1634px">RECENT ACTIVITIES</h2>
<p class="section-lede" style="top:1679px">Lorem Ipsum is simply dummy text of the printing and typesetting industry. Lorem Ipsum has been the industry's standard dummy text ever since the 1500s</p>
<div class="btn" style="left:938px;top:1661px;width:163px;height:37px;font-size:11px">View more activities</div>

<article class="activity" style="left:100px">
  <div class="photo" role="img" aria-label="Wooden longtail boats on a tropical beach" style="background:linear-gradient(180deg,#2f9ad6 0%,#56b8d8 45%,#4cc3b8 65%,#d8c588 100%)"></div>
  <h4>ALGARVE HOLIDAYS</h4>
  <div class="loc">&#9679; City name, Country name : 864899</div>
  <div class="price"><span>From <b>$ 1,500.00</b></span><span class="stars">★★★★☆</span></div>
</article>
<article class="activity" style="left:354px">
  <div class="photo" role="img" aria-label="Resort pool lit up at night" style="background:linear-gradient(180deg,#0b0b12 0%,#1a1a22 40%,#8a5a26 65%,#1f8fb0 85%,#0d3b4a 100%)"></div>
  <h4>ALGARVE HOLIDAYS</h4>
  <div class="loc">&#9679; City name, Country name : 864899</div>
  <div class="price"><span>From <b>$ 1,500.00</b></span><span class="stars">★★★★☆</span></div>
</article>
<article class="activity" style="left:610px">
  <div class="photo" role="img" aria-label="Seaside cabana lounge on a wooden deck" style="background:linear-gradient(180deg,#6f7fa8 0%,#b6a3b9 35%,#6a86a0 55%,#5e4f48 100%)"></div>
  <h4>ALGARVE HOLIDAYS</h4>
  <div class="loc">&#9679; City name, Country name : 864899</div>
  <div class="price"><span>From <b>$ 1,500.00</b></span><span class="stars">★★★★☆</span></div>
</article>
<article class="activity" style="left:866px">
  <div class="photo" role="img" aria-label="Kayak on clear blue water" style="background:linear-gradient(180deg,#2fa0b8 0%,#46b7c4 45%,#d8643a 60%,#2a9aae 80%,#1c7c90 100%)"></div>
  <h4>ALGARVE HOLIDAYS</h4>
  <div class="loc">&#9679; City name, Country name : 864899</div>
  <div class="price"><span>From <b>$ 1,500.00</b></span><span class="stars">★★★★☆</span></div>
</article>

<h2 class="section-title" style="top:2155px">CHOOSE YOUR FAVORITE</h2>
<ul class="favorites" style="left:100px"><li>Algarve holidays</li><li>Alicante car hire</li><li>Amsterdam flights</li><li>Bangkok flights</li><li>Benidorm holidays</li></ul>
<ul class="favorites" style="left:272px"><li>Blackpool hotels</li><li>Cuba holidays</li><li>Cyprus holidays</li><li>Dubai holidays</li><li>Dubai hotels</li></ul>
<ul class="favorites" style="left:433px"><li>Faro car hire</li><li>Gran Canaria holidays</li><li>Lanzarote holidays</li><li>Las Vegas holidays</li><li>London hotels</li></ul>
<ul class="favorites" style="left:628px"><li>Majorca car hire</li><li>Majorca holidays</li><li>Malaga car hire</li><li>Manchester hotels</li><li>Marrakech holidays</li></ul>
<ul class="favorites" style="left:812px"><li>Mexico holidays</li><li>New York flights</li><li>New York holidays</li><li>Orlando flights</li><li>Orlando holidays</li></ul>
<ul class="favorites" style="left:982px"><li>Paris hotels</li><li>Sharm el Sheikh holidays</li><li>Sydney flights</li><li>Tenerife holidays</li><li>UK car hire</li></ul>

<div class="footer-rule"></div>
<div class="copyright">© 2017. Rovanix. All rights reserved.</div>
<div class="social-label">Connect with our social network :</div>
<div class="social" style="left:904px;background:#2f6aa8"></div>
<div class="social" style="left:944px;background:#1f6f8f"></div>
<div class="social" style="left:984px;background:#f0a030"></div>
<div class="social" style="left:1024px;background:#3aa7dc"></div>
<div class="social" style="left:1064px;background:#d92b2b"></div>
<p class="footer-note">Lorem Ipsum is simply dummy text of the printing and typesetting industry. Lorem Ipsum has been the industry's standard dummy text ever since the 1500s, when an unknown printer took a galley of type and scrambled it to make a type specimen book. It has survived not only five centuries, but also the leap into electronic typesetting, remaining essentially unchanged. It was popu-larised in the 1960s with the release of Dravolet sheets containing Lorem Ipsum passages...</p>

</body>
</html>
```